A New and modern Business Card for Tarwick Trade Solutions Ltd

New and modern Logo and Business Card Attached is the current logo/business card designCurrently the business is called "Tarwick & Co." or TTS Ltd for short. This is subject to change.This business specialises in Telecoms and Energy. We work with the major networks (QV, K7, etc) and also offer Energy Products saving clients money off their energy bills.These are business to business services.The current design incorporates a Pheonix, indicating rebirth, starting something new.We would like to maintain the Phoenix element but a newer modern style.We love colours in the logo 3 max.The aim of this is to be ultra slick and modern. I envisage Tarwick & Co. on one side of the card with long descriptions on the other side.Side 1:TTS Ltd/Logo?Side 2:TTS Ltd/Logo/Graphic?Brogan & Co.Name:Address:Phone:Email:The design is mostly flexible but must incorporate a Phoenix.For example "Tarwick & Co." with a block phoenix behind the text...up to you.

Industry/Entity Type

Telecommunications

Contact Information for Business Card

Tarwick & Co.
Address:
Name:
Phone:
Email:

Logo Text

Tarwick & Co.

Colors
33a6d7
0792cd
acd037
9bcb3c
f78f20
fece3e

Requirements
Must have
• Phoenix
• 3/4 colours max
• Blue representing Technology (wireless)
• Green for Eco Energy
• Orange for Phoenix
• White business card background
Should not have
• phoenix must not all be red/ orange fire, we are a technology service company and the phoenix colours must represent this. Fire is not representative of our company.

```html
<!DOCTYPE html>
<html lang="en">
<head>
<meta charset="utf-8">
<title>Tarwick &amp; Co. — Business Card</title>
<link rel="stylesheet" href="https://fonts.googleapis.com/css2?family=Questrial&family=Roboto:wght@400;700&display=swap">
<style>
  :root {
    --page: #c9c9c9;
    --card-dark: #4a4b4f;
    --card-light: #ffffff;
    --ink: #3f3f42;
    --blue: #21409a;
    --green: #acd037;
    --white: #ffffff;
  }
  * { box-sizing: border-box; margin: 0; padding: 0; }
  html, body {
    width: 1200px; height: 930px; overflow: hidden;
    background: var(--page);
  }
  .canvas {
    position: relative; width: 1200px; height: 930px;
  }
  .card {
    position: absolute; left: 250px; width: 700px; height: 400px;
    box-shadow: 0 6px 18px rgba(0,0,0,0.18);
    overflow: hidden;
  }
  .card--front { top: 45px; background: var(--card-dark); }
  .card--back { top: 485px; background: var(--card-light); }

  .brand {
    position: absolute; display: flex; align-items: center;
    font-family: "Questrial", sans-serif; font-weight: 400;
    letter-spacing: 0.5px; white-space: nowrap;
  }
  .brand__square { display: block; flex: none; }
  .card--front .brand {
    left: 50%; top: 50%; transform: translate(-50%, -50%);
    font-size: 58px; color: var(--white); gap: 22px;
  }
  .card--front .brand__square { width: 46px; height: 46px; background: var(--green); }
  .card--back .brand {
    left: 40px; top: 48px; font-size: 34px; color: var(--ink); gap: 14px;
  }
  .card--back .brand__square { width: 28px; height: 28px; background: var(--green); }

  .person {
    position: absolute; right: 48px; top: 122px; text-align: right;
  }
  .person__name {
    font-family: "Roboto", sans-serif; font-weight: 700; font-size: 24px;
    color: var(--blue); letter-spacing: 0.3px;
  }
  .person__role {
    font-family: "Questrial", sans-serif; font-size: 14px; color: var(--ink);
    margin-top: 1px;
  }
  .divider {
    position: absolute; left: 150px; right: 48px; top: 190px;
    height: 1.5px; background: var(--blue);
  }
  .contacts {
    position: absolute; left: 60px; top: 214px; list-style: none;
    font-family: "Questrial", sans-serif; font-size: 15px; color: var(--ink);
  }
  .contacts li { display: flex; align-items: center; gap: 12px; height: 22px; }
  .contacts svg { width: 13px; height: 13px; flex: none; }
  .address {
    position: absolute; right: 48px; top: 218px; text-align: right;
    font-family: "Questrial", sans-serif; font-size: 15px; line-height: 22px;
    color: var(--ink); font-style: normal;
  }
  .swoosh { position: absolute; left: 0; bottom: 0; width: 700px; height: 400px; }
</style>
</head>
<body>
<main class="canvas">
  <section class="card card--front" aria-label="Card front">
    <div class="brand"><span class="brand__square"></span>Tarwick &amp; Co.</div>
  </section>

  <section class="card card--back" aria-label="Card back">
    <svg class="swoosh" viewBox="0 0 700 400" aria-hidden="true">
      <path d="M0,400 L0,386 L500,350 C535,347 545,322 580,320 L700,318 L700,400 Z" fill="var(--blue)"/>
      <path d="M0,377 L492,341" stroke="var(--green)" stroke-width="5" fill="none"/>
    </svg>

    <div class="brand"><span class="brand__square"></span>Tarwick &amp; Co.</div>

    <div class="person">
      <div class="person__name">DANIEL HARLOW</div>
      <div class="person__role">Director</div>
    </div>
    <div class="divider"></div>

    <ul class="contacts">
      <li>
        <svg viewBox="0 0 16 16"><path d="M4 1 L6.5 4.5 L5 6.5 C6 8.5 7.5 10 9.5 11 L11.5 9.5 L15 12 L13 15 C7 14.5 1.5 9 1 3 Z" fill="var(--blue)"/></svg>
        +612 9400 1200
      </li>
      <li>
        <svg viewBox="0 0 16 16"><rect x="4" y="1" width="8" height="5" fill="var(--blue)"/><rect x="1" y="6" width="14" height="6" rx="1" fill="var(--blue)"/><rect x="4" y="10" width="8" height="5" fill="var(--blue)" stroke="#fff" stroke-width="1"/></svg>
        +612 9400 1201
      </li>
      <li>
        <svg viewBox="0 0 16 16"><rect x="1.5" y="3.5" width="13" height="9" fill="none" stroke="var(--blue)" stroke-width="1.5"/><path d="M1.5 3.5 L8 9 L14.5 3.5" fill="none" stroke="var(--blue)" stroke-width="1.5"/></svg>
        mail@tarwick.com.au
      </li>
      <li>
        <svg viewBox="0 0 16 16"><circle cx="8" cy="8" r="6.5" fill="none" stroke="var(--blue)" stroke-width="1.3"/><ellipse cx="8" cy="8" rx="3" ry="6.5" fill="none" stroke="var(--blue)" stroke-width="1.1"/><path d="M1.5 8 H14.5 M2.5 5 H13.5 M2.5 11 H13.5" stroke="var(--blue)" stroke-width="1"/></svg>
        www.tarwick.com.au
      </li>
    </ul>

    <address class="address">
      40-48 Harbour Lane<br>
      Sydney NSW 2000 Australia
    </address>
  </section>
</main>
</body>
</html>
```